Property Investment eBook Cover

I am a long established Australian property investment adviser, analyst and consultant who is now in semi-retired mode and have re-branded to reflect a more casual and personal approach to advising my property investor clients. I am writing a 'revised edition' to a book written in partnership with my father 20 years ago and need an eBook Cover for this new edition. The eBook will be uploaded to all the regular Australian providers (Corvex Slate, Pebble Ureader, Navi, Leafmarta)

The 3 key elements in the book cover are:

Title: The Harvest Rule of Land. The word 'Property' should be larger and more prominent. eg "The Wealth Power of" could be 1/3 the size of "Property" - with both justified left

Edition: Sydney 2021. "Sydney 2021" should be the focus and dominant imagery of the eBook cover and more prominent than the Title or Author

Author: Colin Marwick, The Housing Examiner. The word "Author" should not appear. "The Housing Examiner" should appear underneath Colin Marwick and justified to Colin Marwick, therefore a smaller font.

The cover should be simple, but eye-catching. No property images, more of an abstract background, than a background with an image. Our preferred colour palette is more blues/greens. Prefer SerifFonts

Copy of book published 20 years ago attached for reference only

```html
<!DOCTYPE html>
<html lang="en">
<head>
<meta charset="utf-8">
<title>The Harvest Rule of Land — Sydney 2021</title>
<link rel="stylesheet" href="https://fonts.googleapis.com/css2?family=Cinzel:wght@400&family=EB+Garamond:ital,wght@0,400;1,400&family=Jost:wght@700&display=swap">
<style>
  :root {
    --stage: #e9e9e9;
    --paper: #ffffff;
    --paper-edge: #eaf4f4;
    --ink: #0d0d0d;
    --green-deep: #0a1f12;
    --green-mid: #0c6b2c;
    --green-bright: #00e864;
  }
  html, body {
    margin: 0;
    width: 1200px;
    height: 800px;
    overflow: hidden;
    background: var(--stage);
  }
  .book-cover {
    position: absolute;
    left: 375px;
    top: 40px;
    width: 450px;
    height: 720px;
    display: block;
  }
  .title-lead, .edition-label, .author-name { font-family: "EB Garamond", Georgia, serif; }
  .title-lead { font-size: 40px; fill: var(--ink); }
  .title-main { font-family: "Jost", "Futura", sans-serif; font-weight: 700; font-size: 96px; }
  .edition-label { font-style: italic; font-size: 26px; fill: var(--ink); }
  .edition-city { font-family: "Cinzel", "Trajan Pro", serif; font-size: 57px; fill: var(--ink); }
  .edition-year { font-family: "Jost", "Futura", sans-serif; font-weight: 700; font-size: 60px; }
  .author-name { font-family: "Cinzel", "Trajan Pro", serif; font-size: 43px; fill: var(--ink); }
  .author-role { font-family: "Jost", "Futura", sans-serif; font-weight: 700; font-size: 22px; fill: var(--ink); }
</style>
</head>
<body>
<svg class="book-cover" viewBox="0 0 450 720" xmlns="http://www.w3.org/2000/svg" aria-label="The Harvest Rule of Land, Sydney 2021 edition, by Colin Marwick">
  <defs>
    <radialGradient id="cover-glow" cx="0.6" cy="0.4" r="0.85">
      <stop offset="0" stop-color="var(--paper)"/>
      <stop offset="0.55" stop-color="#f7fbfb"/>
      <stop offset="1" stop-color="var(--paper-edge)"/>
    </radialGradient>
    <linearGradient id="title-shine" x1="0" y1="0" x2="1" y2="0">
      <stop offset="0" stop-color="var(--green-deep)"/>
      <stop offset="0.3" stop-color="var(--green-mid)"/>
      <stop offset="0.55" stop-color="var(--green-bright)"/>
      <stop offset="0.8" stop-color="var(--green-mid)"/>
      <stop offset="1" stop-color="var(--green-deep)"/>
    </linearGradient>
    <linearGradient id="year-shine" x1="0" y1="0" x2="1" y2="0">
      <stop offset="0" stop-color="var(--green-mid)"/>
      <stop offset="1" stop-color="var(--ink)"/>
    </linearGradient>
  </defs>

  <rect class="cover-background" role="img" aria-label="Abstract background of fine pale teal lines radiating from behind the title" width="450" height="720" fill="url(#cover-glow)"/>

  <g class="title">
    <text class="title-lead" x="30" y="161" textLength="276" lengthAdjust="spacingAndGlyphs">The Harvest Rule of</text>
    <text class="title-main" x="32" y="243" fill="url(#title-shine)">LAND</text>
  </g>

  <g class="edition">
    <text class="edition-label" x="32" y="293">Edition:</text>
    <text class="edition-city" x="30" y="350" textLength="236" lengthAdjust="spacingAndGlyphs">SYDNEY</text>
    <text class="edition-year" x="284" y="350" textLength="135" lengthAdjust="spacingAndGlyphs" fill="url(#year-shine)">2021</text>
  </g>

  <g class="author">
    <text class="author-name" x="30" y="639" textLength="390" lengthAdjust="spacingAndGlyphs">COLIN MARWICK</text>
    <text class="author-role" x="31" y="673" textLength="386" lengthAdjust="spacing">THE HOUSING EXAMINER</text>
  </g>
</svg>
</body>
</html>
```